Design and Renovation Company Luxury Business Card

I want to create a luxury business card for a Design and Renovation Firm . We will use our current logo. The company name is 528BUILDA. We do not want anything standard. We need a very unique concept.
Please see uploaded inspiration. I really like the textured paper option. I would like the card to be thick with debossing, and/or embossing options. The logo has orange in it but I would like to see the card with and without the orange. I think the orange may make the company feel less high-end. The goal is to elevate the logo not match its vibe per se of the logo. We want something very unique, not standard at all!
I would like a space for :
Logo,
Name,
Position,
Email,
Office number,
Website Address,
Business Address,
Thank you!
Have fun!
Target Market(s)
Home owners Age 35 +
Industry/Entity Type
Design and Renovation
Contact Information for Business Card
Logo, Name, Position, Email, Office number, Website Address, Business Address,.
Colors
Designer to choose colors to be used in the design.
Requirements
Must have
- A luxury designer feel. Must be black or dark grey but open to other luxury ideas.
Nice to have
- Gold, silver, black embossing or debossing. Textured paper design.
Should not have
- A cheap look and feel.

```html
<!DOCTYPE html>
<html lang="en">
<head>
<meta charset="utf-8">
<title>528BUILDA Business Card</title>
<link rel="stylesheet" href="https://fonts.googleapis.com/css2?family=Arimo:wght@400;700&display=swap">
<style>
  :root {
    --stage: #d9d9d9;
    --stage-edge: #bdbdbd;
    --charcoal: #2f2f2f;
    --charcoal-deep: #262626;
    --pattern-tone: #1e1e1e;
    --orange: #e48a1e;
    --white: #ffffff;
    --soft-white: #f2f2f2;
  }
  * { box-sizing: border-box; margin: 0; padding: 0; }
  html, body { width: 1200px; height: 800px; overflow: hidden; }
  body {
    background: radial-gradient(circle at 40% 30%, #ececec 0%, var(--stage) 55%, var(--stage-edge) 100%);
    position: relative;
    font-family: "Arimo", Arial, sans-serif;
  }
  .card {
    position: absolute;
    top: 245px;
    width: 540px;
    height: 309px;
    border-radius: 22px;
    overflow: hidden;
    box-shadow: 0 10px 28px rgba(0,0,0,0.28);
  }
  .card-front { left: 45px; background: var(--charcoal); }
  .card-back { left: 615px; background: var(--charcoal-deep); }

  /* front */
  .brand-block {
    position: absolute;
    left: 0; top: 0; width: 100%; height: 165px;
    display: flex; align-items: center; justify-content: center;
  }
  .brand-text { display: flex; flex-direction: column; align-items: center; }
  .brand-name {
    font-weight: 700;
    font-size: 52px;
    line-height: 1;
    color: var(--white);
  }
  .brand-tagline {
    margin-top: 10px;
    font-weight: 400;
    font-size: 15px;
    color: var(--soft-white);
  }
  .band-rule {
    position: absolute; left: 0; top: 166px; width: 100%; height: 3px;
    background: var(--white);
  }
  .contact-band {
    position: absolute; left: 0; top: 173px; width: 100%; bottom: 0;
    background: var(--orange);
    display: flex; align-items: center; justify-content: center;
    color: var(--white);
  }
  .person { text-align: right; padding-right: 22px; }
  .person-name { font-weight: 700; font-size: 23px; line-height: 1.1; }
  .person-role { font-size: 17px; line-height: 1.2; }
  .person-email { font-size: 15px; margin-top: 14px; }
  .band-divider { width: 2px; height: 84px; background: var(--white); }
  .details { padding-left: 22px; font-size: 15px; line-height: 1.35; }
  .details-row { display: flex; align-items: center; gap: 7px; }
  .details-row svg { width: 12px; height: 12px; flex: none; }

  /* back */
  .texture-field {
    position: absolute; inset: 0;
    background: linear-gradient(135deg, var(--charcoal) 0%, var(--pattern-tone) 60%, var(--charcoal-deep) 100%);
  }
  .back-mark {
    position: absolute; right: 40px; bottom: 100px;
  }
  .back-mark .brand-name { font-size: 22px; }
</style>
</head>
<body>
  <section class="card card-front" aria-label="Business card front">
    <div class="brand-block">
      <div class="brand-text">
        <span class="brand-name">528BUILDA</span>
        <span class="brand-tagline">Design and Renovation Firm</span>
      </div>
    </div>
    <div class="band-rule"></div>
    <div class="contact-band">
      <div class="person">
        <div class="person-name">Marcus Hale</div>
        <div class="person-role">President</div>
        <div class="person-email">name@528BUILDA.com</div>
      </div>
      <div class="band-divider"></div>
      <div class="details">
        <div>4170 Ashford Lane</div>
        <div>Glen Harbor, NY 11020</div>
        <div class="details-row">
          <svg viewBox="0 0 12 12" aria-hidden="true"><path d="M2.5 1 L4.5 1 L5.3 3.6 L4 4.6 Q5 6.8 7.4 8 L8.4 6.7 L11 7.5 L11 9.5 Q10.5 11 9 11 Q1 10 1 2.5 Q1 1 2.5 1Z" fill="#fff"/></svg>
          <span>(512) 6290-4418</span>
        </div>
        <div class="details-row">
          <svg viewBox="0 0 12 12" aria-hidden="true"><circle cx="6" cy="6" r="5" fill="none" stroke="#fff" stroke-width="1.4"/><path d="M1 6 H11 M6 1 Q3 6 6 11 Q9 6 6 1" fill="none" stroke="#fff" stroke-width="1"/></svg>
          <span>www.528BUILDA.com</span>
        </div>
      </div>
    </div>
  </section>

  <section class="card card-back" aria-label="Business card back">
    <div class="texture-field" role="img" aria-label="Debossed repeating pattern of small dark squares across the card"></div>
    <div class="back-mark">
      <span class="brand-name">528BUILDA</span>
    </div>
  </section>
</body>
</html>
```